IT Freelancer (Consulting, trainer and project manager) needed letterhead

As a freelancer for IT Trainingswhip, consulting and project management I need a letterhead design. What is desired is a design that fits the existing logo (see Annex). It is functional, reliable, and equal time wirkenn Agil and modern. The whole is in color, as well as printed out to make a good impression on a black and white printer. The whole is to the existing Cooperate design (business card, homepage, logo) fit. Therefore, the choice of colors.
Updates

Target Market(s)

Customers such as medium-sized enterprises, training institutions

Industry/Entity Type

Consulting

Colors
0455a3
3277b5
85abd2
cfdfed
34a6d7
32a6d6
249fd4
0792cd
85cae6

Requirements
Must have
• Must include logo (see Annex) address (Brunnerweg 14, 95617 Musterstadt, Germany). Must seriously and act simultaneously Agil. Design should (even) be adaptable (signature, address, etc.) design must look good on a black / white laser

```html
<!DOCTYPE html>
<html lang="de">
<head>
<meta charset="utf-8">
<title>Briefbogen – Matthias Kessler</title>
<link href="https://fonts.googleapis.com/css2?family=Lato:wght@400;700;900&display=swap" rel="stylesheet">
<style>
  :root{
    --navy:#0455a3;
    --blue:#3277b5;
    --sky:#249fd4;
    --cyan:#34c8e6;
    --ice:#85cae6;
    --ink:#1c1c1c;
    --stage:#e6e6e6;
    --paper:#ffffff;
  }
  *{box-sizing:border-box;margin:0;padding:0}
  html,body{width:1200px;height:978px;overflow:hidden;background:var(--stage)}
  body{font-family:"Lato",Arial,sans-serif;color:var(--ink)}
  .letterhead{
    position:absolute;left:280px;top:36px;width:640px;height:906px;
    background:var(--paper);box-shadow:0 4px 18px rgba(0,0,0,.18);overflow:hidden;
  }
  .edge-marks{position:absolute;left:0;top:0}
  .sender-line{
    position:absolute;left:58px;top:86px;font-size:7.5px;letter-spacing:.1px;color:#333;white-space:nowrap;
  }
  .contact{
    position:absolute;right:170px;top:82px;font-size:10.5px;line-height:13px;color:#222;font-style:normal;white-space:nowrap;
  }
  .contact .row{display:flex;align-items:center;gap:5px}
  .contact svg{width:8px;height:8px;flex:none}
  .contact .gap{height:4px}
  .divider{position:absolute;right:152px;top:82px;width:1px;height:86px;background:var(--navy)}
  .brand{
    position:absolute;right:26px;top:78px;width:112px;display:flex;flex-direction:column;align-items:center;gap:8px;
  }
  .brand-dot{width:50px;height:50px;border-radius:50%;background:var(--sky)}
  .brand-name{
    font-weight:900;color:var(--navy);font-size:15px;line-height:16px;text-align:center;letter-spacing:.6px;text-transform:uppercase;
  }
  .footer-rule{position:absolute;left:0;right:0;bottom:44px;height:2px;background:var(--sky)}
  .footer-band{
    position:absolute;left:0;right:0;bottom:0;height:38px;background:var(--navy);
    display:flex;align-items:center;padding-left:170px;
  }
  .footer-band .web{color:#fff;font-size:11px;letter-spacing:.2px}
</style>
</head>
<body>
<main class="letterhead">
  <svg class="edge-marks" width="40" height="190" viewBox="0 0 40 190" aria-hidden="true">
    <polygon points="0,0 16,0 16,54 0,60" fill="var(--navy)"/>
    <polygon points="0,66 16,60 16,110 0,116" fill="var(--sky)"/>
    <polygon points="0,122 16,116 16,144 0,150" fill="var(--cyan)"/>
    <polygon points="0,156 16,150 16,168 0,174" fill="var(--ice)"/>
  </svg>

  <p class="sender-line">Matthias Kessler · Brunnerweg 14 · 95617 Musterstadt · Deutschland</p>

  <address class="contact">
    <div>Brunnerweg 14</div>
    <div>95617 Musterstadt</div>
    <div>Deutschland</div>
    <div class="gap"></div>
    <div class="row"><svg viewBox="0 0 10 10"><path d="M2 1l2 2-1 1.2c.6 1.3 1.5 2.2 2.8 2.8L7 6l2 2-1.2 1.2C4.5 9 1 5.5.8 2.2z" fill="var(--sky)"/></svg>512 004 2730</div>
    <div class="row"><svg viewBox="0 0 10 10"><rect x="1" y="3" width="8" height="5" rx="1" fill="var(--sky)"/><rect x="3" y="1" width="4" height="2.5" fill="var(--sky)"/></svg>512 004 2731</div>
    <div class="row"><svg viewBox="0 0 10 10"><rect x="1" y="2" width="8" height="6" fill="var(--sky)"/><path d="M1 2l4 3.5L9 2" stroke="#fff" stroke-width=".9" fill="none"/></svg>info@matthiaskessler.de</div>
  </address>

  <div class="divider"></div>

  <div class="brand">
    <div class="brand-dot"></div>
    <div class="brand-name">Matthias<br>Kessler</div>
  </div>

  <div class="footer-rule"></div>
  <footer class="footer-band"><span class="web">www.matthiaskessler.de</span></footer>
</main>
</body>
</html>
```